Kickbut Home Page Design built to Sell

We need a new home page layout. The website is working now but we need a refresh. Our business has slowed down since a few years ago. We need to show we build ecommerce and membership websites. Here is the page now: https://www.brelvoxstudio.graphics/new-home/

Target Market(s)

Women, solopreneurs, artists, politicians

Industry/Entity Type

Design Agency

Number of Pages Required

1 page

Font styles to use
Sans Serif

Colors
b8a6cd
fabb94
acd136
00a990

Requirements
Must have
• Video header
Section for text and Step process similar to this website: https://quintarelweb.com/ [This is out sister company]
Places for images.
Call to action lead gen form and Get a quote.
The menu should show WEB, PRINT, VIDEO
Nice to have
• I LOVE this company: https://tarnwickly.com/guide/
Area for testimonials
Should not have
• We don't want a duplicate of https://quintarelweb.com/

```html
<!DOCTYPE html>
<html lang="en">
<head>
<meta charset="utf-8">
<title>Brelvoxstudio – Graphics Web Video Consultants</title>
<link href="https://fonts.googleapis.com/css2?family=Oswald:wght@400;500;600&family=Jost:wght@400;500;600&family=Montserrat:wght@500;600&display=swap" rel="stylesheet">
<style>
:root{
  --green:#00a990;
  --green-deep:#0d9a85;
  --teal-dark:#17574e;
  --lime:#acd136;
  --peach:#fabb94;
  --lilac:#b8a6cd;
  --ink:#1d1d1d;
  --text:#3a3a3a;
  --line:#9a9a9a;
  --soft:#f4f4f3;
  --white:#ffffff;
}
*{box-sizing:border-box;margin:0;padding:0}
html,body{width:1200px;height:4655px;overflow:hidden}
body{position:relative;background:var(--white);font-family:"Jost",sans-serif;color:var(--text)}
.abs{position:absolute}
.heading{font-family:"Oswald",sans-serif;font-weight:500;color:var(--ink);font-size:23px;letter-spacing:.2px}
.heading .accent{color:var(--green)}
.btn{position:absolute;display:flex;align-items:center;justify-content:center;font-family:"Oswald",sans-serif;font-weight:500;font-size:14px;color:var(--white);border-radius:5px;letter-spacing:.2px}

/* hero */
.hero-bg{position:absolute;left:0;top:0;width:1200px;height:730px}
.brand{position:absolute;left:172px;top:38px;color:var(--white)}
.brand-name{font-family:"Jost",sans-serif;font-weight:500;font-size:40px;letter-spacing:1px;line-height:1}
.brand-tag{font-family:"Jost",sans-serif;font-size:10.5px;letter-spacing:2.4px;margin-top:6px}
.nav{position:absolute;top:52px;right:172px;display:flex;gap:32px;font-family:"Oswald",sans-serif;font-weight:500;font-size:15px;color:var(--white)}
.hero-title{position:absolute;left:172px;top:202px;font-family:"Oswald",sans-serif;font-weight:500;font-size:32px;line-height:43px;color:var(--white);letter-spacing:.3px}
.hero-sub{position:absolute;left:172px;top:310px;width:500px;font-size:17px;line-height:29px;color:var(--white)}
.btn-white{background:var(--white);color:var(--ink)}
.btn-outline{border:2px solid var(--white)}
.video-frame{position:absolute;left:717px;top:260px;width:416px;height:336px}

/* about */
.about-photo{position:absolute;left:654px;top:800px;width:546px;height:476px;clip-path:polygon(8% 0,100% 0,100% 100%,0 100%);background:linear-gradient(135deg,#7c8e93,#c9c1b5 45%,#5a5550)}
.about-text{position:absolute;left:172px;top:916px;width:478px;font-size:12.5px;line-height:27px;color:var(--text)}
.about-tag{position:absolute;left:172px;top:1116px;font-family:"Jost",sans-serif;font-weight:500;font-size:13px;color:var(--ink)}

/* services */
.service{position:absolute;top:1466px;width:290px;text-align:center}
.service svg{display:block;margin:0 auto}
.service h3{font-family:"Oswald",sans-serif;font-weight:500;font-size:16px;color:var(--ink);margin-top:20px}
.service p{font-size:12.5px;line-height:24px;margin-top:12px;padding:0 10px}

/* process */
.process-band{position:absolute;left:0;top:1930px;width:1200px;height:835px}
.process-art{position:absolute;left:630px;top:2160px;width:570px;height:410px;border-radius:30px;background:linear-gradient(120deg,rgba(200,225,238,0) 0%,#7a96c8 30%,#e2894c 55%,#5b3d8a 80%,rgba(200,225,238,.3) 100%);opacity:.75}
.process{position:absolute;left:172px;top:2160px;width:408px;color:var(--white)}
.process h2{font-family:"Oswald",sans-serif;font-weight:500;font-size:23px}
.process h4{font-family:"Oswald",sans-serif;font-weight:500;font-size:19px;margin-top:30px}
.process p{font-size:12px;line-height:21px;margin-top:9px;text-align:justify}

/* contact */
.contact-photo{position:absolute;left:0;top:2801px;width:560px;height:488px;background:linear-gradient(90deg,#3b4450 0%,#8a6a4c 35%,#c69a6c 60%,rgba(255,255,255,0) 100%)}
.field{position:absolute;border:1.5px solid #8d8d8d;border-radius:4px;font-size:14px;color:var(--ink);padding:14px 11px}

/* testimonials */
.card{position:absolute;top:3462px;width:270px;height:401px;background:var(--white);box-shadow:0 3px 14px rgba(0,0,0,.12);border-radius:4px;overflow:hidden;text-align:center}
.card .photo{height:206px;background:linear-gradient(160deg,#8f9b95,#d4cfc5 55%,#6f6a63)}
.card h3{font-family:"Montserrat",sans-serif;font-weight:600;font-size:14px;letter-spacing:2px;color:var(--ink);margin-top:28px}
.card p{font-size:11.5px;line-height:23px;padding:0 22px;margin-top:10px}
.card.dark{background:linear-gradient(170deg,#55575a,#2a2b2d 70%)}
.card.dark h3,.card.dark p{color:#e8e8e8}
.card.dark .quote{font-family:"Oswald",sans-serif;font-size:90px;line-height:1;color:var(--white);margin-top:115px;height:70px}

/* newsletter & footer */
.news{position:absolute;left:172px;top:4218px;font-size:27px}
.news-box{position:absolute;left:647px;top:4210px;width:379px;height:52px;border:1.5px solid #9a9a9a;border-radius:6px;overflow:hidden}
.news-box span{position:absolute;left:14px;top:16px;font-size:12px;color:var(--ink)}
.news-box b{position:absolute;right:0;top:0;width:131px;height:100%;background:var(--green);color:var(--white);font-family:"Oswald",sans-serif;font-weight:500;font-size:15px;display:flex;align-items:center;justify-content:center}
.foot-brand{position:absolute;left:172px;top:4400px;color:var(--green)}
.foot-brand .brand-name{font-size:50px}
.foot-brand .brand-tag{font-size:12px;letter-spacing:3px}
.foot-col{position:absolute;top:4345px;font-size:14px;line-height:23.5px;color:#555}
.foot-col h5{font-family:"Jost",sans-serif;font-weight:500;font-size:17px;color:var(--ink);margin-bottom:12px}
.copyright{position:absolute;left:0;top:4590px;width:1200px;height:65px;background:var(--green);display:flex;align-items:center;justify-content:center;color:var(--white);font-size:14px;font-weight:500}
</style>
</head>
<body>

<!-- hero -->
<svg class="hero-bg" viewBox="0 0 1200 730" aria-hidden="true">
  <defs>
    <linearGradient id="heroGrad" x1="0" y1="0" x2="1" y2="1">
      <stop offset="0" stop-color="#11a18b"/>
      <stop offset="1" stop-color="#00a990"/>
    </linearGradient>
  </defs>
  <path d="M0 0H1200V520C1120 548 1010 560 900 590C780 622 700 610 560 600C420 590 320 620 240 660C170 700 90 725 0 715Z" fill="url(#heroGrad)"/>
</svg>

<div class="brand">
  <div class="brand-name">BRELVOXSTUDIO</div>
  <div class="brand-tag">GRAPHICS WEB VIDEO CONSULTANTS</div>
</div>
<nav class="nav"><span>HOME</span><span>WEB</span><span>PRINT</span><span>VIDEO</span><span>CONTACT</span></nav>

<h1 class="hero-title">LEAD GENERATING WEBSITES THAT MOVE<br>YOUR BUSINESS FORWARD</h1>
<p class="hero-sub">Your Company Deserves a Website That Can Inspire People To Take Action</p>
<div class="btn btn-white" style="left:172px;top:401px;width:170px;height:52px">GET A FREE QUOTE</div>
<div class="btn btn-outline" style="left:352px;top:401px;width:170px;height:52px">VIEW OUR WORK</div>

<svg class="video-frame" viewBox="0 0 416 336" role="img" aria-label="Video header: showreel of agency web projects on a desktop screen">
  <rect x="0" y="0" width="416" height="265" rx="8" fill="#2d2f33"/>
  <rect x="12" y="14" width="392" height="222" fill="#6f7f86"/>
  <rect x="0" y="245" width="416" height="28" rx="4" fill="#d7d8da"/>
  <path d="M180 273H236L244 318H172Z" fill="#c9cacc"/>
  <rect x="140" y="316" width="136" height="10" rx="5" fill="#bfc0c2"/>
  <circle cx="208" cy="125" r="34" fill="none" stroke="#fff" stroke-width="5"/>
  <path d="M196 105L228 125L196 145Z" fill="#fff"/>
</svg>

<!-- about -->
<h2 class="heading abs" style="left:172px;top:855px">WE ARE A <span class="accent">WEB DESIGN AGENCY</span></h2>
<p class="about-text">We help brands sell online with beautifully designed websites and effective digital marketing strategies that deliver results &amp; help your business grow.<br>Quintarel Designs is a New England web design agency providing high quality, professional and reliable website - webpage design and graphic design services to individuals, nonprofits, small - medium sized businesses, and political campaigns. We are a small team of highly professional web consultants with over 20 years of knowledge and experience and we'd love to help you too!</p>
<p class="about-tag">DESIGN IS THE SILENT AMBASSADOR TO YOUR BRAND</p>
<div class="btn" style="left:172px;top:1178px;width:122px;height:51px;background:var(--lime)">CONTACT US</div>
<div class="about-photo" role="img" aria-label="Photo of two designers working together at a laptop under a desk lamp"></div>

<!-- services -->
<h2 class="heading abs" style="left:0;top:1379px;width:1200px;text-align:center">OUR <span class="accent">BRELVOXSTUDIO SERVICES</span></h2>

<div class="service" style="left:162px">
  <svg width="150" height="132" viewBox="0 0 150 132" aria-hidden="true">
    <path d="M70 4C108 0 146 30 146 66C146 104 108 128 70 128C34 128 6 108 6 74C6 36 34 8 70 4Z" fill="var(--green)"/>
    <rect x="43" y="42" width="64" height="36" rx="5" fill="none" stroke="#fff" stroke-width="4"/>
    <text x="75" y="66" text-anchor="middle" font-family="Jost,sans-serif" font-size="16" font-weight="600" fill="#fff">www</text>
    <path d="M78 72L78 98L85 91L91 102L96 99L90 88L99 88Z" fill="#fff"/>
  </svg>
  <h3>WEBSITE MAINTENANCE</h3>
  <p>Want to keep your business growing? Your website is crucial to your growth and success. When operating seamlessly with your goals.</p>
</div>
<div class="btn" style="left:249px;top:1780px;width:106px;height:47px;background:var(--green)">CONTACT US</div>

<div class="service" style="left:457px">
  <svg width="150" height="132" viewBox="0 0 150 132" aria-hidden="true">
    <path d="M78 4C116 4 146 36 144 70C142 106 110 128 72 128C36 128 6 104 6 68C6 32 40 4 78 4Z" fill="var(--lime)"/>
    <rect x="50" y="54" width="50" height="34" rx="3" fill="none" stroke="#fff" stroke-width="4"/>
    <path d="M62 54L70 40H92" fill="none" stroke="#fff" stroke-width="4"/>
    <path d="M62 64H88M62 74H88" stroke="#fff" stroke-width="3"/>
    <circle cx="60" cy="96" r="4" fill="#fff"/><circle cx="90" cy="96" r="4" fill="#fff"/>
  </svg>
  <h3>WORKSHOPS</h3>
  <p>We offer workshops to business, schools, non-profits, and organizations. We can taylor the workshop to your organizations if needed.</p>
</div>
<div class="btn" style="left:548px;top:1780px;width:106px;height:47px;background:var(--lime)">CONTACT US</div>

<div class="service" style="left:757px">
  <svg width="150" height="132" viewBox="0 0 150 132" aria-hidden="true">
    <path d="M80 4C118 8 146 40 142 74C138 108 106 130 70 126C34 122 6 98 8 64C10 28 44 0 80 4Z" fill="var(--peach)"/>
    <rect x="46" y="44" width="54" height="40" rx="3" fill="none" stroke="#fff" stroke-width="4"/>
    <path d="M66 84V96M56 96H76" stroke="#fff" stroke-width="3"/>
    <path d="M82 64L82 98L90 90L97 102L103 99L96 87L106 87Z" fill="#fff"/>
  </svg>
  <h3>ARTIST WEBSITE</h3>
  <p>When you are in the art world you need to show your craft to get exposure, gigs and sales. We love working with artists that value good design!</p>
</div>
<div class="btn" style="left:845px;top:1780px;width:106px;height:47px;background:var(--peach)">CONTACT US</div>

<!-- process -->
<svg class="process-band" viewBox="0 0 1200 835" aria-hidden="true">
  <defs>
    <linearGradient id="procGrad" x1="0" y1="0" x2="1" y2="0">
      <stop offset="0" stop-color="var(--teal-dark)"/>
      <stop offset=".5" stop-color="#1d6a61"/>
      <stop offset=".68" stop-color="#8fb8c6"/>
      <stop offset="1" stop-color="#c6e0ee"/>
    </linearGradient>
  </defs>
  <path d="M0 250C120 240 220 130 330 60C420 5 520 20 620 80C720 140 840 150 920 90C1010 20 1100 -10 1200 40V740C1120 790 1000 830 880 820C760 810 700 720 560 690C420 660 320 720 220 770C140 810 60 790 0 770Z" fill="url(#procGrad)"/>
</svg>
<div class="process-art" role="img" aria-label="Illustration of colourful website designs shown on a desktop monitor and floating pages"></div>
<div class="process">
  <h2>OUR BRELVOXSTUDIO PROCESS</h2>
  <h4>STEP 1:</h4>
  <p>When you are in the art world you need to show your craft to get exposure, gigs and sales. We love working with artists that value good design!</p>
  <h4>STEP 2:</h4>
  <p>We create logos for all kinds of companies and brands. A logo can be a nameplate or a monogram, emblem, symbol or signet. A logo can take a week or a year to develop.</p>
  <h4>STEP 3:</h4>
  <p>We offer workshops to business, schools, non-profits, and organizations. We can taylor the workshop to your organizations if needed.</p>
</div>

<!-- contact -->
<div class="contact-photo" role="img" aria-label="Photo of a desktop computer showing the agency website on a wooden desk"></div>
<h2 class="heading abs" style="left:618px;top:2863px">CONTACT <span class="accent">FORM</span></h2>
<div class="field" style="left:618px;top:2918px;width:199px;height:49px">Name</div>
<div class="field" style="left:831px;top:2918px;width:195px;height:49px">Phone</div>
<div class="field" style="left:618px;top:2978px;width:408px;height:49px">Email</div>
<div class="field" style="left:618px;top:3039px;width:408px;height:85px">Message</div>
<div class="btn" style="left:618px;top:3148px;width:112px;height:45px;background:var(--green)">GET A QUOTE</div>

<!-- testimonials -->
<h2 class="heading abs" style="left:0;top:3379px;width:1200px;text-align:center">OUR <span class="accent">TESTIMONIALS</span></h2>
<div class="card" style="left:172px">
  <div class="photo" role="img" aria-label="Photo of a smiling client using her phone at a desk"></div>
  <h3>GOOD WORK</h3>
  <p>This website and SEO audit is specifically designed for businesses and organizations who are working to develop, implement or improve their website and online marketing strategy.</p>
</div>
<div class="card dark" style="left:465px" role="img" aria-label="Photo of a bearded client in a dark shirt behind the testimonial">
  <div class="quote">&rdquo;</div>
  <h3 style="margin-top:21px">GREAT SERVICE</h3>
  <p>This website and SEO audit is specifically designed for businesses and organizations who are working to develop, implement or improve their website and online marketing strategy.</p>
</div>
<div class="card" style="left:757px">
  <div class="photo" role="img" aria-label="Photo of a smiling client in glasses seated at a table"></div>
  <h3>GOOD WORK</h3>
  <p>This website and SEO audit is specifically designed for businesses and organizations who are working to develop, implement or improve their website and online marketing strategy.</p>
</div>

<!-- newsletter band -->
<svg class="abs" style="left:0;top:3900px" width="1200" height="320" viewBox="0 0 1200 320" aria-hidden="true">
  <defs>
    <linearGradient id="softGrad" x1="0" y1="0" x2="0" y2="1">
      <stop offset="0" stop-color="var(--soft)"/>
      <stop offset=".6" stop-color="var(--soft)"/>
      <stop offset="1" stop-color="#ffffff"/>
    </linearGradient>
  </defs>
  <path d="M0 90C150 150 300 160 470 110C650 60 800 20 960 40C1060 52 1140 70 1200 90V320H0Z" fill="url(#softGrad)"/>
</svg>
<h2 class="heading news">SUBSCRIBE TO <span class="accent">OUR NEWSLETTER:</span></h2>
<div class="news-box"><span>Email Address</span><b>SUBSCRIBE</b></div>

<!-- footer -->
<div class="foot-brand">
  <div class="brand-name">BRELVOXSTUDIO</div>
  <div class="brand-tag">GRAPHICS WEB VIDEO CONSULTANTS</div>
</div>
<div class="foot-col" style="left:542px">
  <h5>Quick Links</h5>
  BLOG<br>PRAISE<br>INTERNSHIPS<br>WEBSITE AUDITS<br>Local Business Profile<br>Resource
</div>
<div class="foot-col" style="left:708px">
  <h5>Pages</h5>
  WHO WE ARE<br>OUR CLIENTS<br>OUR PROCESS<br>OUR WORK<br>CONTACT<br>SERVICES
</div>
<div class="foot-col" style="left:858px">
  <h5>Additional Resources</h5>
  FAQ<br>Privacy policy<br>Terms and conditions
</div>
<div class="copyright">Copyrights &copy; 2021 Brelvoxstudio. All Rights Reserved.</div>

</body>
</html>
```